Need webdesign for service company that provides Car hiring service and transit service

We need a web design for a company that provides airport transit services and transport services including Limo, Corporate cars, Disability transit, Family transit service. We need is a simple and professional design.

Below is site which we like and also offer the same service http://www.ridelarkway.com.au/
Updates

Project Deadline Extended
Reason: Waiting for the Feedback from multiple stakeholders. Need the time to select and approve the design

Target Market(s)

Tourism, Travel

Industry/Entity Type

Airport

Number of Pages Required

3 page

Font styles to use
Decorative
Script

Requirements
Must have
• Simple and Professional, Site we like http://www.ridelarkway.com.au/ and also need to mobile friendly
Should not have
• Shouldn't have too many images

```html
<!DOCTYPE html>
<html lang="en">
<head>
<meta charset="utf-8">
<title>Ridewell – Private &amp; Business Transport</title>
<link rel="stylesheet" href="https://fonts.googleapis.com/css2?family=Poppins:wght@300;400;500;600&family=Open+Sans:wght@400&display=swap">
<style>
  :root {
    --ink: #1b1b1b;
    --muted: #555;
    --dark: #2f2f2f;
    --panel: #050505;
    --button: #757071;
    --line: #dcdcdc;
    --band: #f6f6f6;
    --footer: #d4d4d4;
    --white: #ffffff;
  }
  * { box-sizing: border-box; margin: 0; padding: 0; }
  html, body { width: 1078px; height: 1200px; overflow: hidden; background: var(--white); }
  body { font-family: "Poppins", sans-serif; color: var(--ink); position: relative; }

  .site-header { position: absolute; left: 0; top: 0; width: 1078px; height: 108px; border-bottom: 1px solid #e6e6e6; box-shadow: 0 2px 4px rgba(0,0,0,.04); }
  .brand { position: absolute; left: 72px; top: 28px; display: flex; align-items: center; gap: 12px; }
  .brand-dot { width: 44px; height: 44px; border-radius: 50%; background: var(--dark); flex: none; }
  .brand-text { display: flex; flex-direction: column; }
  .brand-name { font-size: 29px; font-weight: 400; line-height: 1; color: var(--ink); letter-spacing: .5px; }
  .brand-tag { font-size: 8px; color: var(--muted); letter-spacing: .4px; margin-top: 4px; }

  .header-tools { position: absolute; top: 31px; left: 684px; display: flex; align-items: center; }
  .social { display: flex; gap: 10px; margin-right: 14px; }
  .social span { width: 16px; height: 16px; background: #e4e4e4; border-radius: 2px; display: block; }
  .menu-btn { width: 34px; height: 32px; background: var(--dark); border-radius: 3px; display: flex; flex-direction: column; justify-content: center; align-items: center; gap: 3px; margin-right: 7px; }
  .menu-btn i { width: 12px; height: 2px; background: var(--white); display: block; }
  .search-btn { width: 34px; height: 32px; border: 1px solid var(--line); border-radius: 3px; display: flex; align-items: center; justify-content: center; margin-right: 8px; }
  .phone-box { height: 32px; border: 1px solid var(--line); border-radius: 3px; display: flex; align-items: center; padding: 0 6px 0 9px; gap: 5px; font-size: 13px; font-weight: 500; }

  .intro { position: absolute; top: 130px; width: 100%; text-align: center; }
  .intro h1 { font-size: 25px; font-weight: 400; letter-spacing: 1px; }
  .intro p { font-size: 11px; letter-spacing: .8px; margin-top: 2px; font-weight: 500; }

  .hero { position: absolute; left: 0; top: 195px; width: 1078px; height: 440px;
    background: linear-gradient(180deg, #a9b4bb 0%, #7f8a93 20%, #55606c 45%, #3d4149 75%, #4b4d52 100%); }
  .quote-panel { position: absolute; left: 74px; top: 66px; width: 294px; height: 317px; background: var(--panel); padding: 0 11px; }
  .quote-panel h2 { font-size: 19px; font-weight: 400; color: var(--white); text-align: center; margin: 27px 0 30px; letter-spacing: .3px; }
  .quote-panel h2 b { font-weight: 500; }
  .field { background: var(--white); height: 36px; border-radius: 2px; font-size: 11px; padding: 0 13px; display: flex; align-items: center; margin-bottom: 8px; }
  .field.vehicles { height: 68px; flex-direction: column; align-items: flex-start; justify-content: center; gap: 7px; margin-bottom: 10px; }
  .field.vehicles span { padding-left: 5px; }
  .cta { width: 271px; height: 39px; background: var(--button); color: var(--white); font-size: 16px; font-weight: 500; letter-spacing: .8px; display: flex; align-items: center; justify-content: center; border-radius: 2px; margin-left: -2px; }

  .services { position: absolute; top: 674px; left: 72px; display: flex; gap: 16px; }
  .service-card { position: relative; width: 219px; height: 176px; padding-top: 21px; }
  .service-card::before { content: ""; position: absolute; left: 0; right: 0; top: 21px; bottom: 0; border: 2px solid #ececec; }
  .service-icon { position: absolute; left: 50%; top: 0; transform: translateX(-50%); width: 69px; height: 45px; background: var(--dark); display: flex; align-items: center; justify-content: center; z-index: 1; }
  .service-card h3 { position: relative; text-align: center; font-size: 15px; font-weight: 400; letter-spacing: .5px; margin-top: 42px; white-space: nowrap; }
  .service-card h3 b { font-weight: 500; }
  .service-card p { position: relative; text-align: center; font-size: 10.5px; font-weight: 300; color: var(--muted); line-height: 18px; margin: 8px 12px 0; }

  .about { position: absolute; top: 894px; left: 0; width: 1078px; height: 216px; background: var(--band); }
  .about h2 { position: absolute; left: 72px; top: 25px; font-size: 22px; font-weight: 400; }
  .about p { position: absolute; left: 73px; top: 68px; width: 580px; font-family: "Open Sans", sans-serif; font-size: 10.6px; letter-spacing: -0.1px; color: #444; line-height: 22.8px; }
  .about-frame { position: absolute; left: 690px; top: 35px; width: 309px; height: 165px; background: #cdcdcd; padding: 7px; }
  .about-photo { width: 100%; height: 100%; background: linear-gradient(180deg, #a7adb2 0%, #6f767c 50%, #2a2d31 80%, #6d7176 100%); }

  .site-footer { position: absolute; left: 0; top: 1156px; width: 1078px; height: 44px; background: var(--footer); display: flex; align-items: center; justify-content: center; font-size: 12px; font-weight: 500; }
</style>
</head>
<body>
  <header class="site-header">
    <div class="brand">
      <div class="brand-dot"></div>
      <div class="brand-text">
        <span class="brand-name">RIDEWELL</span>
        <span class="brand-tag">SMART WAY TO KEEP MOVING</span>
      </div>
    </div>
    <div class="header-tools">
      <div class="social"><span></span><span></span><span></span><span></span></div>
      <div class="menu-btn"><i></i><i></i><i></i></div>
      <div class="search-btn">
        <svg width="14" height="14" viewBox="0 0 14 14"><circle cx="5.5" cy="5.5" r="4.3" fill="none" stroke="#333" stroke-width="1.5"/><line x1="8.7" y1="8.7" x2="13" y2="13" stroke="#333" stroke-width="1.6"/></svg>
      </div>
      <div class="phone-box">123-456-7890
        <svg width="18" height="18" viewBox="0 0 18 18"><circle cx="9" cy="9" r="9" fill="#9a9a9a"/><path d="M6 4.5l1.8 2.4-1 1.2c.7 1.4 1.7 2.4 3.1 3.1l1.2-1 2.4 1.8-1 1.8c-3.6-.2-7.3-3.9-7.5-7.5z" fill="#fff"/></svg>
      </div>
    </div>
  </header>

  <section class="intro">
    <h1>PRIVATE &amp; BUSINESS</h1>
    <p>PERSONALISED TRANSPORT SERVICES</p>
  </section>

  <section class="hero" role="img" aria-label="Photo of a dark blue sedan parked by a seaside railing with a silver car behind">
    <form class="quote-panel">
      <h2>GET INSTANT <b>QUOTE</b></h2>
      <div class="field">Origin</div>
      <div class="field">Destination</div>
      <div class="field vehicles">Show other vehicles<span>+&nbsp;&nbsp;&nbsp;Add</span></div>
      <div class="cta">GET STARTED NOW!</div>
    </form>
  </section>

  <section class="services">
    <article class="service-card">
      <div class="service-icon"><svg width="30" height="22" viewBox="0 0 30 22"><path d="M6 9l3-6h12l3 6h3v9h-3v3h-4v-3H10v3H6v-3H3V9z" fill="#fff"/><rect x="10" y="4.5" width="10" height="4" fill="#2f2f2f"/><circle cx="8" cy="13" r="2" fill="#2f2f2f"/><circle cx="22" cy="13" r="2" fill="#2f2f2f"/></svg></div>
      <h3>CORPORATE <b>CARS</b></h3>
      <p>Lorem ipsum dolor sit amet, co nsectetuer adipiscing elit, sed diam nonummy nibh euismod Lorem ipsum dolor sit</p>
    </article>
    <article class="service-card">
      <div class="service-icon"><svg width="34" height="26" viewBox="0 0 34 26"><circle cx="6" cy="4" r="3" fill="#fff"/><rect x="3" y="8" width="6" height="17" fill="#fff"/><path d="M13 14l3-5h10l3 5h3v7h-3v3h-3v-3H17v3h-3v-3h-2v-7z" fill="#fff"/><circle cx="16" cy="17" r="1.5" fill="#2f2f2f"/><circle cx="27" cy="17" r="1.5" fill="#2f2f2f"/></svg></div>
      <h3>LIMO <b>SERVICE</b></h3>
      <p>Lorem ipsum dolor sit amet, co nsectetuer adipiscing elit, sed diam nonummy nibh euismod Lorem ipsum dolor sit</p>
    </article>
    <article class="service-card">
      <div class="service-icon"><svg width="30" height="24" viewBox="0 0 30 24"><path d="M5 10l3-8h14l3 8h2v10h-3v3h-4v-3H10v3H6v-3H3V10z" fill="#fff"/><rect x="9" y="4" width="12" height="5" fill="#2f2f2f"/><rect x="6" y="14" width="4" height="2" fill="#2f2f2f"/><rect x="20" y="14" width="4" height="2" fill="#2f2f2f"/></svg></div>
      <h3>DISABILITY <b>TRANSIT</b></h3>
      <p>Lorem ipsum dolor sit amet, co nsectetuer adipiscing elit, sed diam nonummy nibh euismod Lorem ipsum dolor sit</p>
    </article>
    <article class="service-card">
      <div class="service-icon"><svg width="30" height="26" viewBox="0 0 30 26"><rect x="9" y="1" width="12" height="3" fill="none" stroke="#fff" stroke-width="1.4"/><rect x="4" y="5" width="22" height="14" rx="2" fill="none" stroke="#fff" stroke-width="1.6"/><line x1="4" y1="11" x2="26" y2="11" stroke="#fff" stroke-width="1.4"/><circle cx="9" cy="21" r="2.6" fill="none" stroke="#fff" stroke-width="1.5"/><circle cx="21" cy="21" r="2.6" fill="none" stroke="#fff" stroke-width="1.5"/></svg></div>
      <h3>FAMILY <b>TRANSIT SERVICE.</b></h3>
      <p>Lorem ipsum dolor sit amet, co nsectetuer adipiscing elit, sed diam nonummy nibh euismod Lorem ipsum dolor sit</p>
    </article>
  </section>

  <section class="about">
    <h2>ABOUT US</h2>
    <p>Lorem ipsum dolor sit amet, consectetuer adipiscing elit, sed diam nonummy nibh euismod Lorem ipsum dolor sit Lorem ipsum dolor sit amet, consectetuer adipiscing elit, sed diam nonummy nibh euismod Lorem ipsum dolor sit Lorem ipsum dolor sit amet, consectetuer adipiscing elit, sed diam nonummy nibh euismod Lorem ipsum dolor sit Lorem ipsum dolor sit amet, consectetuer adipiscing elit, sed diam nonummy nibh euismod Lorem ipsum dolor sit Lorem ipsum dolor sit amet, consectetuer adipiscing elit, sed diam nonummy nibh</p>
    <div class="about-frame">
      <div class="about-photo" role="img" aria-label="Photo of a black station wagon driving on a road"></div>
    </div>
  </section>

  <footer class="site-footer">Copyright © 2017 RIDEWELL. All right reserved.</footer>
</body>
</html>
```